4th Generation Family Business Needs a New Card Design!

We are a family owned 4th Generation company. We are based in the Sydney, Australia area and we are desperately in need of a more modern and classy card. We are monumental masons who design, supply & erect lasting memorials throughout cemeteries in Sydney. Our customers are normally in a period of grieving. I have attached logo files that will need to be implemented on the card. Company was established 1935. Australian Owned and Operated. Card needs to be designed to PIXO.com specification.

Target Market(s)

Our target market is based upon people that a grieving for family members that have passed away. We also deal with alot of companies that own and operate cemeteries.

Industry/Entity Type

Business

Contact Information for Business Card

Simon Harcourt, Operations Manager, 0417293086, simon@harcourtmemorials.com.au
Lewis Harcourt, Director, 0491630572, lewis@harcourtmemorials.com.au
Phone # 02 9561 3048
Website: www.harcourtmemorials.com.au
Address: Suite 17, 8 Palfrey Lane, West Carlow, Sydney NSW 2156

Font styles to use
Serif
Decorative
Script

Requirements
Must have
• Would like to see the logo nicely implemented with a modern design. Embossed lettering would be a nice additive.

```html
<!DOCTYPE html>
<html lang="en">
<head>
<meta charset="utf-8">
<title>Harcourt Memorials – Business Card</title>
<link rel="stylesheet" href="https://fonts.googleapis.com/css2?family=Cinzel:wght@400;700&family=Tinos:wght@400;700&display=swap">
<style>
  :root {
    --backdrop: #232323;
    --card-black: #000000;
    --card-white: #ffffff;
    --gold: #e8bd2a;
    --ink-light: #ffffff;
    --ink-dark: #000000;
  }
  * { margin: 0; padding: 0; box-sizing: border-box; }
  html, body { width: 1200px; height: 1076px; overflow: hidden; }
  body {
    background: var(--backdrop);
    position: relative;
    font-family: "Tinos", "Times New Roman", serif;
  }
  .card {
    position: absolute;
    left: 170px;
    width: 860px;
    height: 496px;
    box-shadow: 0 10px 24px rgba(0,0,0,0.6);
    overflow: hidden;
  }
  .card--back { top: 30px; background: var(--card-black); }
  .card--front { top: 550px; display: flex; }

  .wordmark {
    position: absolute;
    left: 0; right: 0;
    text-align: center;
    font-family: "Cinzel", "Times New Roman", serif;
    font-weight: 400;
    line-height: 1.15;
    letter-spacing: 2px;
  }
  .card--back .wordmark {
    top: 178px;
    font-size: 58px;
    color: var(--ink-light);
  }

  .front-brand {
    position: relative;
    width: 430px;
    height: 100%;
    background: var(--card-white);
  }
  .front-brand .wordmark {
    top: 180px;
    font-size: 46px;
    color: var(--ink-dark);
  }

  .front-details {
    width: 430px;
    height: 100%;
    background: var(--card-black);
    padding: 88px 0 0 26px;
    color: var(--ink-light);
  }
  .person-name {
    font-family: "Cinzel", "Times New Roman", serif;
    font-weight: 700;
    font-size: 27px;
    line-height: 1;
    letter-spacing: 0.5px;
  }
  .person-role {
    color: var(--gold);
    font-size: 22px;
    line-height: 1.1;
    margin-top: 0;
  }
  .address {
    margin-top: 76px;
    font-size: 22px;
    line-height: 31px;
  }
  .contact-list {
    list-style: none;
    margin-top: 8px;
    font-size: 21px;
    line-height: 30px;
  }
  .contact-list .label { color: var(--gold); font-weight: 700; }
  .website {
    margin-top: 8px;
    color: var(--gold);
    font-size: 21px;
  }
</style>
</head>
<body>
  <section class="card card--back" aria-label="Card back">
    <div class="wordmark">Harcourt<br>Memorials</div>
  </section>

  <section class="card card--front" aria-label="Card front">
    <div class="front-brand">
      <div class="wordmark">Harcourt<br>Memorials</div>
    </div>
    <div class="front-details">
      <p class="person-name">Simon Harcourt</p>
      <p class="person-role">Operations Manager</p>
      <p class="address">Suite 17, 8 Palfrey Lane,<br>West Carlow, Sydney NSW 2156</p>
      <ul class="contact-list">
        <li><span class="label">M:</span> 0417293086</li>
        <li><span class="label">P:</span> 02 9561 3048</li>
        <li><span class="label">E:</span> simon@harcourtmemorials.com.au</li>
      </ul>
      <p class="website">www.harcourtmemorials.com.au</p>
    </div>
  </section>
</body>
</html>
```